Business card design for holistic health care clinic

We need a double-sided business card design for our holistic health care clinic that integrates our logo design and also its color scheme. My business is called Valmira. It is an integrative medicine clinic. You have already done the logo for me. Please ensure an elegant and upscale design that is not cluttered, but still has all the necessary information (please see below for details).

Target Market(s)

Wellness, fitness, rehabilitation for educated, well-traveled open-minded clients who are focused on natural, organic, balanced and preventive healthcare and lifestyle.

Industry/Entity Type

Medical

Contact Information for Business Card

Modern, clean.

Number of Pages Required

1 page

Font styles to use
Serif
Sans Serif

Colors

Designer to choose colors to be used in the design.

Requirements
Must have
• Logo on one side, all other information on the other side.
• Other information should include:
• Tobias Wrenfeld - DOE, CPT, LMT
• 4100 East Marrow Drive
• Austin, TX 78119
• 512 555 0148
• 818 555 0192
• info@ValmiraHealth.example
• t.wrenfeld@ValmiraHealth.example
Nice to have
• Darker background on front - but not totally black - shaded/dark gray.

```html
<!DOCTYPE html>
<html lang="en">
<head>
<meta charset="utf-8">
<title>Valmira – Business Card</title>
<link rel="stylesheet" href="https://fonts.googleapis.com/css2?family=Nunito:wght@800&family=Roboto:ital,wght@0,400;0,500;0,700;1,500&family=Roboto+Condensed:wght@700&display=swap">
<style>
  :root {
    --backdrop: #ece8e2;
    --card-dark: #2b2b2b;
    --card-dark-deep: #1f1f1f;
    --brand-blue: #0a8fcc;
    --brand-blue-soft: rgba(255, 255, 255, 0.09);
    --ink-dark: #1d1d1d;
    --ink-light: #ffffff;
  }
  * { margin: 0; padding: 0; box-sizing: border-box; }
  html, body { width: 1200px; height: 960px; overflow: hidden; }
  body { background: var(--backdrop); position: relative; font-family: "Roboto", Arial, sans-serif; }

  .card { position: absolute; width: 600px; height: 342px; overflow: hidden; box-shadow: 0 2px 5px rgba(0,0,0,0.35); }
  .card--front { left: 314px; top: 113px; background: radial-gradient(ellipse at 60% 20%, #333 0%, var(--card-dark) 50%, var(--card-dark-deep) 100%); }
  .card--back { left: 311px; top: 472px; height: 343px; background: var(--brand-blue); }

  .front__tab { position: absolute; left: -6px; top: 45px; width: 15px; height: 39px; border-radius: 6px; background: var(--brand-blue); }
  .front__name { position: absolute; left: 33px; top: 54px; font-family: "Roboto Condensed", Arial, sans-serif; font-weight: 700; font-size: 21px; color: var(--brand-blue); letter-spacing: 0.2px; }
  .front__credentials { font-size: 12px; margin-left: 2px; }

  .wordmark { position: absolute; font-family: "Nunito", Arial, sans-serif; font-weight: 800; line-height: 1; letter-spacing: 0.5px; }
  .front__wordmark { right: 38px; top: 88px; font-size: 50px; color: var(--brand-blue); }
  .front__tagline { position: absolute; right: 41px; top: 141px; font-family: "Nunito", Arial, sans-serif; font-weight: 800; font-size: 14.5px; color: var(--brand-blue); }

  .front__wave { position: absolute; left: 0; top: 0; }

  .contact { position: absolute; left: 34px; top: 218px; color: var(--ink-light); font-size: 14px; line-height: 19px; }
  .contact dt { float: left; font-weight: 700; margin-right: 4px; }
  .contact dd { }
  .contact__address { margin-top: 6px; }

  .back__emblem { position: absolute; }
  .back__wordmark { right: 56px; top: 220px; font-size: 42px; color: var(--ink-dark); }
  .back__tagline { position: absolute; right: 58px; top: 266px; font-family: "Nunito", Arial, sans-serif; font-weight: 800; font-size: 12px; color: var(--ink-dark); }
  .back__motto { position: absolute; right: 57px; top: 285px; font-style: italic; font-weight: 500; font-size: 15px; color: var(--ink-light); }
</style>
</head>
<body>

<section class="card card--front" aria-label="Front of business card">
  <svg class="front__wave" width="600" height="342" viewBox="0 0 600 342" aria-hidden="true">
    <path d="M0,190 C140,168 260,182 360,240 C450,292 520,338 600,342 L0,342 Z" fill="var(--brand-blue)"/>
    <g fill="none" stroke="#262626" stroke-width="2">
      <path d="M0,187 C140,165 262,179 362,237 C452,289 522,335 600,339"/>
      <path d="M0,194 C145,174 270,188 368,244 C456,294 526,338 600,342"/>
      <path d="M20,199 C160,182 280,196 374,250 C460,298 530,340 580,342"/>
    </g>
  </svg>

  <span class="front__tab" aria-hidden="true"></span>
  <h1 class="front__name">TOBIAS WRENFELD <span class="front__credentials">- DOE, CPT, LMT</span></h1>

  <div class="wordmark front__wordmark">VALMIRA</div>
  <p class="front__tagline">Integrative Holistic Medicine</p>

  <dl class="contact">
    <dt>P:</dt><dd>512 555 0148</dd>
    <dt>C:</dt><dd>818 555 0192</dd>
    <dt>E:</dt><dd>t.wrenfeld@ValmiraHealth.example</dd>
    <dt>W:</dt><dd>www.ValmiraHealth.example</dd>
    <dd class="contact__address">4100 East Marrow Drive , Austin, TX 78119</dd>
  </dl>
</section>

<section class="card card--back" aria-label="Back of business card">
  <svg class="back__emblem" width="600" height="343" viewBox="0 0 600 343" aria-hidden="true">
    <circle cx="100" cy="170" r="150" fill="var(--brand-blue-soft)"/>
  </svg>
  <div class="wordmark back__wordmark">VALMIRA</div>
  <p class="back__tagline">Integrative Holistic Medicine</p>
  <p class="back__motto">helping the body help itself</p>
</section>

</body>
</html>
```